Fitness Equipment & Service

I want to make the card eye catching and fun. We are called Corvane Motion Limited and we are based in Wales. We sell, install and service all types of fitness equipment from Skipping ropes, right through the Dumbbells, Kettle bells and Barbells through to state of the art Treadmills, Running Machines and Strength Equipment. We also design and install changing room furniture and lockers.

TYPOGRAPHY
We would like to use Futrura. Futura has an appearance of efficiency and forwardness. The typeface is derived
from simple geometric forms (near-perfect circles, triangles and squares) and is based on strokes of
near-even weight, which are low in contrast. This is most visible in the almost perfectly round stroke of
the o, which is nonetheless slightly ovoid.
The lowercase has tall ascenders, which rise above the cap line. The uppercase
characters present proportions similar to those of classical Roman capitals.

TYPOGRAPHIC CONSIDERATIONS
No Strike though
No Horizontal Scaling
No Drop Shadows
No Effects
Never use less than 120% Leading

OUR CORPORATE COLOURS
BRAND GUIDELINES
We were thinking that our primary colour palette consists of the Acid Green (Pantone 382) and Process Black.

We work closely with tquarly Ltd and would like to include their name on the card somewhere. I have attached images of the other brands that we work with as an idea or the small icons I have included that illustrate what we do?. I have very kindly been given permission to use any of the images off the files that I have included below, so I hope these help. I will include these below. I would be open to suggestions if it made the card more striking Can you do it?
Updates

Hi All, Just wanted to add a few thoughts but you are the guys with the creative visions (thats why are here) We are based in Wales, UK and we would be open to lots of different ideas on a theme but must be eye catching, Bold and FUN. If you can or think that the Welsh or any dragon could be put in there then go for it (its not a must have) We have also added some ideas for colour but again its over to you!! GO FOR IT ! Thanks and look forward to your visions! Owen

Hi All, Just thought I would sen through the contact details that need to be on the card. (if you want to play around with icons instead of the wording twitter, Facebook, go for it): Corvane Motion Limited Owen Pritchard Managing Director Mob: +44 (0)7582 913 406 e-mail: sales@corvanemotion.co.uk Web: Corvanemotion.co.uk twitter: @motionLetterbin Facebook: Corvane Motion Limited

```html
<!DOCTYPE html>
<html lang="en">
<head>
<meta charset="utf-8">
<title>Corvane Motion Limited – Business Card</title>
<link href="https://fonts.googleapis.com/css2?family=Arimo:wght@400;700&display=swap" rel="stylesheet">
<style>
  :root {
    --navy: #1b2a5c;
    --navy-deep: #0f1b45;
    --navy-mid: #2a4690;
    --gold: #b8923a;
    --ink: #3a3a3a;
    --rule: #c9c9c9;
    --paper: #ffffff;
    --paper-shade: #e4e4e4;
    --stage: #efefef;
  }
  html, body {
    margin: 0;
    padding: 0;
    width: 1200px;
    height: 950px;
    overflow: hidden;
    background: var(--stage);
    font-family: "Arimo", Arial, sans-serif;
  }
  .canvas {
    position: relative;
    width: 1200px;
    height: 950px;
  }
  .card {
    position: absolute;
    left: 240px;
    width: 720px;
    height: 411px;
    box-sizing: border-box;
    box-shadow: 0 6px 18px rgba(0,0,0,0.18);
  }

  /* Front */
  .card-front {
    top: 40px;
    background: linear-gradient(160deg, var(--paper) 0%, var(--paper) 55%, var(--paper-shade) 100%);
  }
  .brand-block {
    position: absolute;
    left: 40px;
    top: 70px;
    width: 250px;
    text-align: center;
  }
  .brand-mark {
    width: 140px;
    height: 140px;
    border-radius: 50%;
    margin: 0 auto 26px;
    background: radial-gradient(circle at 40% 35%, var(--navy-mid) 0%, var(--navy-deep) 75%);
  }
  .brand-name {
    margin: 0;
    color: var(--navy);
    font-weight: 700;
    font-size: 22px;
    line-height: 1.25;
    text-transform: uppercase;
  }
  .divider {
    position: absolute;
    left: 320px;
    top: 48px;
    width: 1px;
    height: 300px;
    background: var(--rule);
  }
  .contact-block {
    position: absolute;
    left: 350px;
    top: 56px;
    right: 30px;
  }
  .person-name {
    margin: 0;
    color: var(--navy);
    font-weight: 700;
    font-size: 27px;
    line-height: 1.2;
  }
  .person-role {
    margin: 0 0 16px;
    color: var(--gold);
    font-size: 22px;
    line-height: 1.25;
  }
  .address {
    margin: 0 0 4px;
    font-style: normal;
    color: var(--ink);
    font-size: 20px;
    line-height: 1.25;
  }
  .contact-list {
    list-style: none;
    margin: 0;
    padding: 0;
  }
  .contact-list li {
    display: flex;
    align-items: center;
    gap: 10px;
    color: var(--ink);
    font-size: 20px;
    line-height: 1.3;
  }
  .contact-list svg {
    flex: none;
    width: 16px;
    height: 16px;
    fill: var(--navy);
  }

  /* Back */
  .card-back {
    top: 500px;
    background: linear-gradient(90deg, var(--navy-deep) 0%, var(--navy-mid) 55%, var(--navy) 100%);
  }
  .back-mark {
    position: absolute;
    left: 290px;
    top: 110px;
    width: 140px;
    height: 140px;
    border-radius: 50%;
    background: radial-gradient(circle at 40% 35%, #3a5cb0 0%, var(--navy-deep) 75%);
    border: 3px solid #c7ccd8;
  }
  .back-web {
    position: absolute;
    left: 370px;
    top: 270px;
    display: flex;
    align-items: center;
    gap: 8px;
    margin: 0;
    color: #dfe4ee;
    font-size: 20px;
    letter-spacing: 1px;
    line-height: 1.25;
  }
  .back-web::after {
    content: "";
    display: block;
    width: 40px;
    height: 1px;
    background: #dfe4ee;
  }
</style>
</head>
<body>
<main class="canvas">

  <section class="card card-front" aria-label="Business card front">
    <div class="brand-block">
      <div class="brand-mark" aria-hidden="true"></div>
      <p class="brand-name">CML<br>Corvane Motion Limited</p>
    </div>

    <div class="divider" aria-hidden="true"></div>

    <div class="contact-block">
      <h1 class="person-name">Owen Pritchard</h1>
      <p class="person-role">Managing Director</p>
      <address class="address">27 Harbour Row<br>Aberaeron, SA46 0BT</address>
      <ul class="contact-list">
        <li>
          <svg viewBox="0 0 16 16" aria-hidden="true"><path d="M4 1h8a1 1 0 0 1 1 1v12a1 1 0 0 1-1 1H4a1 1 0 0 1-1-1V2a1 1 0 0 1 1-1zm1 2v9h6V3z"/><circle cx="8" cy="13.5" r=".8" fill="#fff"/></svg>
          +44 (0)7582 913 406
        </li>
        <li>
          <svg viewBox="0 0 16 16" aria-hidden="true"><path d="M1 3h14v10H1zm1.5 1.2v.3L8 8.4l5.5-3.9v-.3zM2.5 6.3v5.4h11V6.3L8 10.2z"/></svg>
          sales@corvanemotion.co.uk
        </li>
        <li>
          <svg viewBox="0 0 16 16" aria-hidden="true"><circle cx="8" cy="8" r="7"/><path d="M1 8h14M8 1c-3 3-3 11 0 14M8 1c3 3 3 11 0 14" stroke="#fff" stroke-width="1" fill="none"/></svg>
          Corvanemotion.co.uk
        </li>
        <li>
          <svg viewBox="0 0 16 16" aria-hidden="true"><rect x="1" y="1" width="14" height="14" rx="2"/></svg>
          @motionLetterbin
        </li>
        <li>
          <svg viewBox="0 0 16 16" aria-hidden="true"><rect x="1" y="1" width="14" height="14" rx="2"/></svg>
          Corvane Motion Limited
        </li>
      </ul>
    </div>
  </section>

  <section class="card card-back" aria-label="Business card back">
    <div class="back-mark" aria-hidden="true"></div>
    <p class="back-web">Corvanemotion.co.uk</p>
  </section>

</main>
</body>
</html>
```